Bref créative
plinth Card and stationary design
logo and stationary
Simple
Martin Fowlby
Agent/Advocate
4150 Harrow Ridge Lane
Suite 238
Greensboro, NC 27516
office- 336-555-0184
martin@plinth7.com
www.plinth7.com
I will upload the logo to use for the card and stationary.
please use the file I upload for the content on the back.
Plinth new logo
card back content

```html
<!DOCTYPE html>
<html lang="en">
<head>
<meta charset="utf-8">
<title>Plinth – Business Card</title>
<link href="https://fonts.googleapis.com/css2?family=Arimo:wght@400;700&display=swap" rel="stylesheet">
<style>
  :root {
    --backdrop: #e9e6ee;
    --card: #ffffff;
    --purple: #5a2d91;
    --purple-soft: #9d88c6;
    --ink: #2a2a2a;
    --rule: #d9d6de;
  }
  html, body {
    margin: 0;
    padding: 0;
    width: 1200px;
    height: 778px;
    overflow: hidden;
    background: var(--backdrop);
    font-family: "Arimo", Arial, sans-serif;
  }
  .card {
    position: absolute;
    left: 168px;
    top: 140px;
    width: 864px;
    height: 497px;
    background: var(--card);
    box-shadow: 0 6px 18px rgba(40, 20, 60, 0.18);
  }
  .brand {
    position: absolute;
    left: 62px;
    top: 150px;
    display: flex;
    align-items: center;
    gap: 18px;
  }
  .brand-mark {
    width: 64px;
    height: 64px;
    background: var(--purple-soft);
  }
  .brand-name {
    font-size: 86px;
    line-height: 1;
    font-weight: 400;
    color: var(--purple);
    letter-spacing: 1px;
  }
  .tagline {
    position: absolute;
    left: 90px;
    top: 322px;
    font-size: 23px;
    color: var(--purple);
    letter-spacing: 0.5px;
  }
  .tagline-rule {
    position: absolute;
    left: 90px;
    top: 312px;
    width: 270px;
    height: 2px;
    background: var(--purple-soft);
  }
  .divider {
    position: absolute;
    left: 430px;
    top: 78px;
    width: 1px;
    height: 336px;
    background: var(--rule);
  }
  .contact {
    position: absolute;
    left: 485px;
    top: 100px;
    color: var(--ink);
  }
  .person-name {
    margin: 0;
    font-size: 31px;
    font-weight: 700;
    color: var(--purple);
  }
  .person-role {
    margin: 6px 0 0;
    font-size: 24px;
    color: var(--purple);
  }
  .address {
    margin: 42px 0 0;
    font-size: 19px;
    line-height: 26px;
    font-style: normal;
  }
  .channels {
    list-style: none;
    margin: 12px 0 0;
    padding: 0;
    font-size: 19px;
    line-height: 26px;
  }
  .channels li {
    display: flex;
    align-items: center;
    gap: 10px;
  }
  .channels svg {
    width: 14px;
    height: 14px;
    fill: var(--ink);
    flex: none;
  }
</style>
</head>
<body>
  <section class="card">
    <div class="brand">
      <div class="brand-mark"></div>
      <span class="brand-name">Plinth</span>
    </div>
    <div class="tagline-rule"></div>
    <div class="tagline">Life, Health &amp; Financial</div>

    <div class="divider"></div>

    <div class="contact">
      <h1 class="person-name">Martin Fowlby</h1>
      <p class="person-role">Agent/Advocate</p>
      <address class="address">
        4150 Harrow Ridge Lane<br>
        Suite 238<br>
        Greensboro, NC 27516
      </address>
      <ul class="channels">
        <li>
          <svg viewBox="0 0 16 16" aria-hidden="true"><path d="M3 1h3l1 4-2 1a9 9 0 0 0 5 5l1-2 4 1v3c0 1-1 2-2 2A13 13 0 0 1 1 3c0-1 1-2 2-2z"/></svg>
          office- 336-555-0184
        </li>
        <li>
          <svg viewBox="0 0 16 16" aria-hidden="true"><path d="M4 0h8a1 1 0 0 1 1 1v14a1 1 0 0 1-1 1H4a1 1 0 0 1-1-1V1a1 1 0 0 1 1-1zm1 2v10h6V2zm3 11a1 1 0 1 0 0 2 1 1 0 0 0 0-2z"/></svg>
          336-555-0927
        </li>
        <li>
          <svg viewBox="0 0 16 16" aria-hidden="true"><path d="M1 3h14v10H1zm1.5 1.5v.4L8 9l5.5-4.1v-.4zm0 2.2v4.8h11V6.7L8 10.8z"/></svg>
          martin@plinth7.com
        </li>
        <li>
          <svg viewBox="0 0 16 16" aria-hidden="true"><path d="M8 0a8 8 0 1 0 0 16A8 8 0 0 0 8 0zm0 1.5c.8 0 1.8 1.8 2.1 5H5.9C6.2 3.3 7.2 1.5 8 1.5zm-2.1 7h4.2c-.3 3.2-1.3 5-2.1 5s-1.8-1.8-2.1-5z"/></svg>
          www.plinth7.com
        </li>
      </ul>
    </div>
  </section>
</body>
</html>
```